Website for Ashcombe Tube Drift

Require a website for a river float in the City of Edmonton. Located on North Saskatchewan River. Will need to be a coded website with incorporated booking system through Fare Harbor software.

Pages include
Home
Pricing
About
FAQ
Contact

Ashcombe Tube Drift is an activity based business that will have customers floating down the North Saskatchewan river in Edmonton AB. The site will have all information needed and a full reservation system. The project was launched to provide people in the Edmonton area a favorite summer activity.

Here are similar websites to reference what our business will be doing and what we are looking for.

mossbankfloatco.com
quillpointpaddles.com

Target Market(s)

Families, Groups, Individuals, Anyone who wants to explore the river

Industry/Entity Type

Activities based business/ Outdoor recreational/ River Float

Coding

Coded - Design and coding required

Number of Pages Required

5+ page

Colors
0054AA
0677BA
7BADD7
CADEEF
E8F1F8
F0912C
F2A743
F7CA91
FBE8D2
FDF5EE

```html
<!DOCTYPE html>
<html lang="en">
<head>
<meta charset="utf-8">
<title>Ashcombe Tube Drift</title>
<link href="https://fonts.googleapis.com/css2?family=Montserrat:wght@700;800&family=Roboto:wght@400;500;700&display=swap" rel="stylesheet">
<style>
:root{
  --sky:#2aa9d6;
  --navy:#062f63;
  --orange:#e0532a;
  --ink:#222;
  --muted:#555;
  --soft:#f4f4f4;
  --black:#111;
  --white:#fff;
}
*{box-sizing:border-box;margin:0;padding:0}
html,body{width:1200px;height:3299px;overflow:hidden}
body{position:relative;font-family:Roboto,sans-serif;color:var(--ink);background:var(--white)}
.abs{position:absolute}
.btn{position:absolute;display:flex;align-items:center;justify-content:center;background:var(--sky);color:#fff;font:500 15px Roboto,sans-serif;border-radius:26px;text-transform:uppercase}
/* header */
.site-header{position:absolute;left:0;top:0;width:1200px;height:90px;background:#fff;z-index:5}
.nav-item{position:absolute;top:0;height:90px;display:flex;align-items:center;font:500 15px Roboto,sans-serif;color:#555;text-transform:uppercase}
.nav-item.active{color:var(--sky)}
.nav-item.active::after{content:"";position:absolute;left:0;right:0;bottom:26px;height:3px;background:var(--sky)}
.nav-sep{position:absolute;top:0;width:1px;height:90px;background:#e2e2e2}
.brand-badge{position:absolute;left:489px;top:-60px;width:222px;height:222px;border-radius:50%;background:#fff;z-index:6;display:flex;flex-direction:column;align-items:center;justify-content:flex-end;padding-bottom:52px}
.brand-mark{width:60px;height:60px;border-radius:50%;background:var(--sky);margin-bottom:8px}
.brand-name{font:800 16px Montserrat,sans-serif;color:var(--navy);text-transform:uppercase;text-align:center;line-height:1.15;width:170px}
.social{position:absolute;width:38px;height:38px;border-radius:50%;border:2px solid var(--sky)}
.social.filled{background:var(--sky)}
.social::after{content:"";position:absolute;left:13px;top:13px;width:8px;height:8px;border-radius:50%;background:var(--sky)}
.social.filled::after{background:#fff}
/* hero */
.hero-photo{position:absolute;left:0;top:90px;width:1200px;height:660px;background:linear-gradient(180deg,#8fa4b8 0%,#b9b2a4 30%,#8a7b66 50%,#4e5f55 65%,#3f6a5c 78%,#6d8f3c 100%)}
.hero-caption{position:absolute;left:310px;top:279px;width:580px;height:140px;background:rgba(120,120,120,.45);border-radius:3px}
.hero-title{position:absolute;left:0;top:312px;width:1200px;text-align:center;font:800 37px Montserrat,sans-serif;color:#fff;letter-spacing:.5px}
.hero-sub{position:absolute;left:0;top:362px;width:1200px;text-align:center;font:500 21px/31px Roboto,sans-serif;color:#fff}
.arrow{position:absolute;width:36px;height:36px;border-radius:50%;display:flex;align-items:center;justify-content:center}
/* pricing */
.h2{font:800 32px Montserrat,sans-serif;color:var(--navy);text-transform:uppercase}
.price-sub{font:700 27px Montserrat,sans-serif;color:var(--orange);text-transform:uppercase}
.features{position:absolute;left:681px;top:1043px;width:400px;display:grid;grid-template-columns:231px 170px;row-gap:11px;font:400 14.5px Roboto,sans-serif;color:#555;list-style:none}
.features li{display:flex;align-items:center;gap:12px;height:19px}
.features svg{flex:none}
/* about */
.about-photo{position:absolute;left:0;top:1387px;width:600px;height:471px;background:linear-gradient(180deg,#8fb0d6 0%,#dfe6ee 35%,#6f7a82 55%,#a48a3a 75%,#8e9a8c 100%)}
.about-panel{position:absolute;left:531px;top:1336px;width:558px;height:445px;background:var(--navy);color:#fff;padding:36px 56px 0 58px}
.about-panel h2{font:800 36px Montserrat,sans-serif;text-transform:uppercase;margin-bottom:22px}
.about-panel p{font:400 14.5px/26px Roboto,sans-serif;margin-bottom:11px}
/* faq */
.faq-item{position:absolute;width:425px;height:51px;background:#fff;box-shadow:0 2px 8px rgba(0,0,0,.12);display:flex;align-items:center;padding-left:17px;font:400 15px Roboto,sans-serif;color:#444}
.faq-toggle{position:absolute;right:4px;top:7px;width:37px;height:37px;background:var(--sky);display:flex;align-items:center;justify-content:center}
/* contact */
.contact-band{position:absolute;left:0;top:2385px;width:1200px;height:540px;background:var(--soft)}
.contact-row{position:absolute;left:135px;display:flex;align-items:center;gap:20px;font:500 15.5px Roboto,sans-serif;color:#333}
.c-icon{width:45px;height:45px;border-radius:50%;background:var(--sky);display:flex;align-items:center;justify-content:center}
.map-frame{position:absolute;left:448px;top:2514px;width:623px;height:333px;background:#fff;box-shadow:0 2px 10px rgba(0,0,0,.15);padding:7px}
.map-area{width:100%;height:100%;background:linear-gradient(160deg,#eef0ee 0%,#e6ebe4 45%,#aac7ec 60%,#e9ede6 72%,#e4ece1 100%)}
/* footer */
.footer{position:absolute;left:0;top:2960px;width:1200px;height:339px;background:var(--black);color:#fff}
.f-head{position:absolute;font:700 15px Roboto,sans-serif;text-transform:uppercase;color:#fff}
.f-line{position:absolute;display:flex;gap:16px;font:400 13.5px/22px Roboto,sans-serif;color:#fff}
.f-line svg{flex:none;margin-top:4px}
.nav-list{position:absolute;left:731px;top:3080px;list-style:none;font:400 14px Roboto,sans-serif}
.nav-list li{display:flex;align-items:center;gap:17px;height:27.5px}
</style>
</head>
<body>

<header class="site-header">
  <a class="nav-item active" style="left:111px">Home</a>
  <span class="nav-sep" style="left:185px"></span>
  <a class="nav-item" style="left:216px">Pricing</a>
  <span class="nav-sep" style="left:307px"></span>
  <a class="nav-item" style="left:337px">About</a>
  <a class="nav-item" style="left:791px">FAQ</a>
  <span class="nav-sep" style="left:843px"></span>
  <a class="nav-item" style="left:865px">Contact</a>
  <span class="social filled" style="left:967px;top:26px" aria-label="Social link"></span>
  <span class="social" style="left:1009px;top:26px" aria-label="Reviews link"></span>
  <span class="social" style="left:1050px;top:26px" aria-label="Photo link"></span>
</header>
<div class="brand-badge">
  <span class="brand-mark"></span>
  <span class="brand-name">Ashcombe Tube Drift</span>
</div>

<section class="hero">
  <div class="hero-photo" role="img" aria-label="City skyline above a river with a bridge and green riverbank"></div>
  <div class="hero-caption"></div>
  <h1 class="hero-title">ASHCOMBE TUBE DRIFT</h1>
  <p class="hero-sub">Float the North Saskatchewan through<br>downtown Edmonton</p>
  <a class="btn" style="left:531px;top:444px;width:136px;height:47px">Book Now</a>
  <span class="arrow" style="left:47px;top:392px;background:#fff"><svg width="12" height="12" viewBox="0 0 12 12"><path d="M8 1 3 6l5 5" fill="none" stroke="#2aa9d6" stroke-width="2"/></svg></span>
  <span class="arrow" style="left:1117px;top:392px;background:var(--sky)"><svg width="12" height="12" viewBox="0 0 12 12"><path d="M4 1l5 5-5 5" fill="none" stroke="#fff" stroke-width="2"/></svg></span>
  <svg class="abs" style="left:0;top:580px" width="1200" height="180" viewBox="0 0 1200 180">
    <path d="M0 80 C120 30 280 10 420 30 C520 45 560 75 620 95 C380 40 160 60 0 120Z" fill="#e0532a"/>
    <path d="M0 125 C200 60 420 40 600 95 C760 140 900 185 1060 140 C1130 115 1180 80 1200 55 L1200 180 L0 180Z" fill="#fff"/>
  </svg>
</section>

<section class="pricing">
  <svg class="abs" style="left:100px;top:790px" width="500" height="500" viewBox="0 0 500 500">
    <circle cx="265" cy="240" r="237" fill="#2aa9d6"/>
    <circle cx="250" cy="247" r="240" fill="#fff"/>
    <path d="M30 190 A237 237 0 0 0 230 485" fill="none" stroke="#e0532a" stroke-width="5"/>
  </svg>
  <div class="abs" style="left:113px;top:800px;width:474px;height:474px;border-radius:50%;background:linear-gradient(180deg,#6fa6e0 0%,#b98a8a 30%,#7f8f6c 55%,#5d8a3d 80%,#7aa040 100%)" role="img" aria-label="Arched pedestrian bridge in front of downtown towers"></div>
  <h2 class="h2 abs" style="left:681px;top:804px">Our Pricing</h2>
  <p class="price-sub abs" style="left:681px;top:852px">Tube and Shuttle</p>
  <p class="abs" style="left:681px;top:910px;font:500 26px Roboto,sans-serif;color:#222">$30<span style="font-size:14px;color:#555">/person</span></p>
  <a class="btn" style="left:802px;top:901px;width:137px;height:49px">Book Now</a>
  <p class="abs" style="left:681px;top:971px;width:360px;font:400 18.5px/29px Roboto,sans-serif;color:#222">We keep our pricing simple and include everything you need:</p>
  <ul class="features">
    <li><svg width="14" height="14" viewBox="0 0 14 14"><circle cx="7" cy="7" r="6" fill="none" stroke="#e0532a" stroke-width="2"/><path d="M4 7h6M7.5 4.5 10 7l-2.5 2.5" fill="none" stroke="#e0532a" stroke-width="2"/></svg>Lifejacket</li>
    <li><svg width="14" height="14" viewBox="0 0 14 14"><circle cx="7" cy="7" r="6" fill="none" stroke="#e0532a" stroke-width="2"/><path d="M4 7h6M7.5 4.5 10 7l-2.5 2.5" fill="none" stroke="#e0532a" stroke-width="2"/></svg>Safety training</li>
    <li><svg width="14" height="14" viewBox="0 0 14 14"><circle cx="7" cy="7" r="6" fill="none" stroke="#e0532a" stroke-width="2"/><path d="M4 7h6M7.5 4.5 10 7l-2.5 2.5" fill="none" stroke="#e0532a" stroke-width="2"/></svg>Paddle</li>
    <li><svg width="14" height="14" viewBox="0 0 14 14"><circle cx="7" cy="7" r="6" fill="none" stroke="#e0532a" stroke-width="2"/><path d="M4 7h6M7.5 4.5 10 7l-2.5 2.5" fill="none" stroke="#e0532a" stroke-width="2"/></svg>Staff assistance</li>
    <li><svg width="14" height="14" viewBox="0 0 14 14"><circle cx="7" cy="7" r="6" fill="none" stroke="#e0532a" stroke-width="2"/><path d="M4 7h6M7.5 4.5 10 7l-2.5 2.5" fill="none" stroke="#e0532a" stroke-width="2"/></svg>Round trip shuttle service</li>
    <li><svg width="14" height="14" viewBox="0 0 14 14"><circle cx="7" cy="7" r="6" fill="none" stroke="#e0532a" stroke-width="2"/><path d="M4 7h6M7.5 4.5 10 7l-2.5 2.5" fill="none" stroke="#e0532a" stroke-width="2"/></svg>Unlimited Fun!</li>
  </ul>
  <a class="btn" style="left:681px;top:1151px;width:138px;height:50px">Book Now</a>
  <p class="abs" style="left:681px;top:1224px;font:400 16.5px Roboto,sans-serif;color:#222">Group of 10 or more? <span style="color:var(--sky);text-decoration:underline">Contact us</span></p>
  <p class="abs" style="left:681px;top:1252px;font:400 14px Roboto,sans-serif;color:#e0302a">*does not include taxes or fees</p>
</section>

<section class="about">
  <div class="about-photo" role="img" aria-label="Downtown skyline above autumn trees and a river valley"></div>
  <div class="about-panel">
    <h2>About Us</h2>
    <p>Float the North Saskatchewan through downtown Edmonton Edmonton’ s Best Summer Activity We provide the lifejacket, paddle, river tube and shuttle service. You just have to show up. Ashcombe Tube Drift was launched to provide people in the Edmonton area a favorite summer activity.</p>
    <p>Nothing is better on a hot summer day, than spending it on the river and seeing Edmonton from a new perspective. Our home base and meeting spot is at Cedar Landing (Map Link)</p>
  </div>
  <a class="btn" style="left:589px;top:1691px;width:138px;height:50px">Book Now</a>
</section>

<section class="faq">
  <h2 class="h2 abs" style="left:0;top:1922px;width:1200px;text-align:center;font-size:34px">FAQ</h2>
  <div class="faq-item" style="left:165px;top:1997px">How do I reserve my float?<span class="faq-toggle"><svg width="12" height="12"><path d="M6 1v10M1 6h10" stroke="#fff" stroke-width="2.5"/></svg></span></div>
  <div class="faq-item" style="left:607px;top:1997px">How do I reserve my float?<span class="faq-toggle"><svg width="12" height="12"><path d="M6 1v10M1 6h10" stroke="#fff" stroke-width="2.5"/></svg></span></div>
  <div class="faq-item" style="left:165px;top:2059px">What safety information should I know?<span class="faq-toggle"><svg width="12" height="12"><path d="M6 1v10M1 6h10" stroke="#fff" stroke-width="2.5"/></svg></span></div>
  <div class="faq-item" style="left:607px;top:2059px">What is included?<span class="faq-toggle"><svg width="12" height="12"><path d="M6 1v10M1 6h10" stroke="#fff" stroke-width="2.5"/></svg></span></div>
  <div class="faq-item" style="left:165px;top:2121px">What should I bring?<span class="faq-toggle"><svg width="12" height="12"><path d="M6 1v10M1 6h10" stroke="#fff" stroke-width="2.5"/></svg></span></div>
  <div class="faq-item" style="left:607px;top:2121px">Where are you located?<span class="faq-toggle"><svg width="12" height="12"><path d="M6 1v10M1 6h10" stroke="#fff" stroke-width="2.5"/></svg></span></div>
  <div class="faq-item" style="left:165px;top:2184px">What time should I arrive?<span class="faq-toggle"><svg width="12" height="12"><path d="M6 1v10M1 6h10" stroke="#fff" stroke-width="2.5"/></svg></span></div>
  <div class="faq-item" style="left:607px;top:2184px">Where should I park?<span class="faq-toggle"><svg width="12" height="12"><path d="M6 1v10M1 6h10" stroke="#fff" stroke-width="2.5"/></svg></span></div>
  <div class="faq-item" style="left:165px;top:2246px">How long does the trip take?<span class="faq-toggle"><svg width="12" height="12"><path d="M6 1v10M1 6h10" stroke="#fff" stroke-width="2.5"/></svg></span></div>
  <div class="faq-item" style="left:607px;top:2246px">What happens if I miss my shuttle?<span class="faq-toggle"><svg width="12" height="12"><path d="M6 1v10M1 6h10" stroke="#fff" stroke-width="2.5"/></svg></span></div>
</section>

<section class="contact">
  <div class="contact-band"></div>
  <h2 class="abs" style="left:0;top:2434px;width:1200px;text-align:center;font:800 34px Montserrat,sans-serif;color:#111">CONTACT US</h2>
  <div class="contact-row" style="top:2549px"><span class="c-icon"><svg width="16" height="16" viewBox="0 0 16 16"><path d="M3 1l3 3-2 2c1 2 3 4 5 5l2-2 3 3-2 3C7 15 1 9 1 3z" fill="#fff"/></svg></span>780XXXXXXX</div>
  <div class="contact-row" style="top:2604px"><span class="c-icon"><svg width="16" height="12" viewBox="0 0 16 12"><rect width="16" height="12" rx="1" fill="#fff"/><path d="M1 1l7 6 7-6" fill="none" stroke="#2aa9d6" stroke-width="1.5"/></svg></span>info@ashcombetubedrift.com</div>
  <div class="contact-row" style="top:2659px"><span class="c-icon"><svg width="14" height="14"><circle cx="7" cy="7" r="4" fill="#fff"/></svg></span>Community Page</div>
  <div class="contact-row" style="top:2714px"><span class="c-icon"><svg width="14" height="14"><circle cx="7" cy="7" r="4" fill="#fff"/></svg></span>Photo Feed</div>
  <div class="contact-row" style="top:2769px"><span class="c-icon"><svg width="14" height="14"><circle cx="7" cy="7" r="4" fill="#fff"/></svg></span>Travel Reviews</div>
  <div class="map-frame"><div class="map-area" role="img" aria-label="Street map of the river valley with the meeting point marked"></div></div>
</section>

<footer>
  <svg class="abs" style="left:0;top:2870px" width="1200" height="100" viewBox="0 0 1200 100">
    <path d="M0 50 C250 -20 480 10 700 50 C900 85 1050 60 1200 15 L1200 30 C1060 80 900 100 700 70 C480 35 250 10 0 70Z" fill="#e0532a"/>
    <path d="M0 60 C250 -10 480 20 700 60 C900 95 1060 80 1200 30 L1200 100 L0 100Z" fill="#111"/>
  </svg>
  <div class="footer"></div>
  <h3 class="f-head" style="left:111px;top:3036px">Connect</h3>
  <div class="f-line" style="left:111px;top:3077px"><svg width="9" height="12" viewBox="0 0 9 12"><path d="M4.5 0A4.5 4.5 0 0 0 0 4.5C0 8 4.5 12 4.5 12S9 8 9 4.5A4.5 4.5 0 0 0 4.5 0z" fill="#2aa9d6"/><circle cx="4.5" cy="4.5" r="1.6" fill="#111"/></svg><span>412 Willowbend Rd, Ashcombe,<br>AB, Canada</span></div>
  <div class="f-line" style="left:111px;top:3132px"><svg width="12" height="12" viewBox="0 0 16 16"><path d="M3 1l3 3-2 2c1 2 3 4 5 5l2-2 3 3-2 3C7 15 1 9 1 3z" fill="#2aa9d6"/></svg><span>780XXXXXXX</span></div>
  <div class="f-line" style="left:111px;top:3160px"><svg width="13" height="10" viewBox="0 0 16 12"><rect width="16" height="12" rx="1" fill="#2aa9d6"/><path d="M1 1l7 6 7-6" fill="none" stroke="#111" stroke-width="1.5"/></svg><span>info@ashcombetubedrift.com</span></div>

  <h3 class="f-head" style="left:374px;top:3036px">Sign up for our mailing list</h3>
  <div class="abs" style="left:374px;top:3084px;width:318px;height:49px;border-radius:25px;background:#fff;display:flex;align-items:center;justify-content:space-between;padding:0 20px;font:400 13.5px Roboto,sans-serif;color:#333">Email Address<svg width="18" height="16" viewBox="0 0 18 16"><path d="M1 7 17 1 12 15 9 9z M9 9 17 1" fill="none" stroke="#2aa9d6" stroke-width="1.4"/></svg></div>
  <svg class="abs" style="left:374px;top:3160px" width="48" height="48" viewBox="0 0 48 48"><path d="M40 14A20 20 0 1 0 44 28" fill="none" stroke="#fff" stroke-width="3"/><path d="M36 8l5 7-8 1" fill="none" stroke="#fff" stroke-width="3"/><text x="24" y="29" text-anchor="middle" font-family="Roboto,sans-serif" font-size="12" font-weight="700" fill="#fff">24/7</text></svg>

  <h3 class="f-head" style="left:731px;top:3036px">Navigation</h3>
  <ul class="nav-list">
    <li><svg width="13" height="13" viewBox="0 0 14 14"><circle cx="7" cy="7" r="7" fill="#2aa9d6"/><path d="M4 7h6M7.5 4.5 10 7l-2.5 2.5" fill="none" stroke="#111" stroke-width="1.6"/></svg>Home</li>
    <li><svg width="13" height="13" viewBox="0 0 14 14"><circle cx="7" cy="7" r="7" fill="#2aa9d6"/><path d="M4 7h6M7.5 4.5 10 7l-2.5 2.5" fill="none" stroke="#111" stroke-width="1.6"/></svg>Pricing</li>
    <li><svg width="13" height="13" viewBox="0 0 14 14"><circle cx="7" cy="7" r="7" fill="#2aa9d6"/><path d="M4 7h6M7.5 4.5 10 7l-2.5 2.5" fill="none" stroke="#111" stroke-width="1.6"/></svg>About</li>
    <li><svg width="13" height="13" viewBox="0 0 14 14"><circle cx="7" cy="7" r="7" fill="#2aa9d6"/><path d="M4 7h6M7.5 4.5 10 7l-2.5 2.5" fill="none" stroke="#111" stroke-width="1.6"/></svg>FAQ</li>
    <li><svg width="13" height="13" viewBox="0 0 14 14"><circle cx="7" cy="7" r="7" fill="#2aa9d6"/><path d="M4 7h6M7.5 4.5 10 7l-2.5 2.5" fill="none" stroke="#111" stroke-width="1.6"/></svg>Contact</li>
  </ul>

  <div class="abs" style="left:909px;top:3042px;width:180px;display:flex;flex-direction:column;align-items:center;gap:12px">
    <span style="width:96px;height:96px;border-radius:50%;background:var(--sky)"></span>
    <span style="font:800 19px/1.15 Montserrat,sans-serif;color:var(--sky);text-align:center;text-transform:uppercase">Ashcombe Tube Drift</span>
  </div>

  <div class="abs" style="left:111px;top:3234px;width:978px;height:1px;background:#444"></div>
  <p class="abs" style="left:0;top:3254px;width:1200px;text-align:center;font:400 13.5px Roboto,sans-serif;color:#fff">© 2022 <b>ASHCOMBE TUBE DRIFT</b> &nbsp;/&nbsp; All Rights Reserved</p>
  <span class="social filled" style="left:967px;top:3244px;border-color:#fff" aria-label="Social link"></span>
  <span class="social" style="left:1009px;top:3244px;border-color:#fff" aria-label="Reviews link"></span>
  <span class="social" style="left:1050px;top:3244px;border-color:#fff" aria-label="Photo link"></span>
</footer>

</body>
</html>
```